Flyer for spiritual retreat (yoga, meditation, reiki, raw food)

I would like a flyer to promote my upcoming retreat and a matching Facebook banner.

The name of the retreat is "OutBloom the Spirit" and the tagline is "retreat into you"

The activities in the retreat include daily meditation, ecstatic dance, spiritual development workshops on intuition, energy healing etc and a reiki session is included.

I would like a flyer designed to promote this, something that is editable as I will be running this multiple times and will need to adjust the flyer to add the dates etc each time.

edit: add that here will be fully catered raw food and juices, and that the retreat price includes all accomodation, meals and workshops.

Please contact me if you need further info. Please also visit my website www.marlavosk.com and www.pagenest.com/koruhaven to see my current events and promotions.

Thank you,

Marla

Reason: Hi all, thank you all for your submissions. Apologies as I am traveling and do not have much access to internet and will review your submissions and provide feedback as soon as possible. Kind regards, Marla.

Target Market(s)

People who like meditation, yoga, fans of tomas brenner and wendell marsh, those interested in personal and spiritual development.

Industry/Entity Type

Health And Wellness

Requirements
Must have
• Please put the included reiki session as as added bonus. Something like "BONUS 30 minute reiki healing session" in a little star/banner/something that stands out.
• Please emphasise the "light" part of OutBloom as I am going for a play on words between in the light and enlightenment.
• Please include placeholder text for place, location, time
• Placeholder for price
• My name (see attached file - can change colour to suit) and website (www.marlavosk.com)
Nice to have
• I prefer rounded designs, curves rather than block designs.
Should not have
• Koru Haven logo

```html
<!DOCTYPE html>
<html lang="en">
<head>
<meta charset="utf-8">
<title>OutBloom the Spirit – Retreat Into You</title>
<link rel="stylesheet" href="https://fonts.googleapis.com/css2?family=Poppins:wght@500;600;700&family=Montserrat:ital,wght@1,800&family=Oswald:wght@400;600&family=Roboto+Condensed:wght@700&family=Great+Vibes&display=swap">
<style>
  :root {
    --navy: #2b3990;
    --sky: #1eaaf1;
    --ink: #1d1d1f;
    --paper: #f2f2f4;
    --white: #ffffff;
    --card: rgba(255,255,255,0.9);
  }
  html, body {
    margin: 0;
    padding: 0;
    overflow: hidden;
    background: var(--paper);
  }
  .flyer {
    position: relative;
    width: 848px;
    height: 1200px;
    overflow: hidden;
    background: var(--paper);
  }
  .flyer-shapes {
    position: absolute;
    inset: 0;
  }
  .host-signature {
    position: absolute;
    left: 440px;
    top: 120px;
    margin: 0;
    font-family: "Great Vibes", cursive;
    font-size: 82px;
    font-weight: 400;
    color: #e9e9ec;
    text-shadow: 2px 2px 3px rgba(0,0,0,0.45);
    transform: rotate(-8deg);
    white-space: nowrap;
  }
  .bonus-text {
    position: absolute;
    left: 645px;
    top: 378px;
    width: 170px;
    margin: 0;
    text-align: center;
    font-family: "Oswald", sans-serif;
    color: var(--white);
    text-transform: uppercase;
    line-height: 1.1;
  }
  .bonus-label {
    display: block;
    font-weight: 600;
    font-size: 30px;
    letter-spacing: 1px;
  }
  .bonus-detail {
    display: block;
    font-size: 17px;
  }
  .event-details {
    position: absolute;
    left: 30px;
    top: 405px;
    width: 270px;
    padding: 16px 20px;
    box-sizing: border-box;
    border-radius: 24px;
    background: var(--card);
    font-family: "Oswald", sans-serif;
    color: var(--ink);
  }
  .event-details dl {
    margin: 0;
    display: grid;
    grid-template-columns: auto 1fr;
    column-gap: 10px;
    row-gap: 3px;
    font-size: 19px;
    line-height: 1.25;
  }
  .event-details dt {
    font-weight: 600;
    color: var(--navy);
    text-transform: uppercase;
  }
  .event-details dd {
    margin: 0;
  }
  .catering-note {
    margin: 10px 0 0;
    padding-top: 8px;
    border-top: 2px solid var(--sky);
    font-size: 15px;
    line-height: 1.3;
  }
  .retreat-title {
    position: absolute;
    left: 0;
    top: 0;
    margin: 0;
    font-family: "Poppins", sans-serif;
    font-weight: 600;
    line-height: 1;
    text-shadow: 2px 2px 0 var(--white), -2px -2px 0 var(--white), 2px -2px 0 var(--white), -2px 2px 0 var(--white), 3px 4px 6px rgba(0,0,0,0.35);
  }
  .retreat-title span {
    position: absolute;
    white-space: nowrap;
  }
  .title-out { left: 300px; top: 640px; font-size: 70px; color: var(--navy); }
  .title-bloom { left: 292px; top: 680px; font-size: 150px; color: var(--navy); letter-spacing: -3px; }
  .title-the { left: 338px; top: 845px; font-size: 72px; color: var(--sky); font-weight: 500; }
  .title-spirit { left: 470px; top: 805px; font-size: 124px; color: var(--sky); letter-spacing: -2px; }
  .tagline {
    position: absolute;
    left: 128px;
    top: 940px;
    margin: 0;
    font-family: "Montserrat", sans-serif;
    font-style: italic;
    font-weight: 800;
    font-size: 54px;
    color: var(--ink);
    white-space: nowrap;
    letter-spacing: 0.5px;
  }
  .activities {
    position: absolute;
    left: 0;
    width: 848px;
    top: 1024px;
    margin: 0;
    padding-right: 30px;
    box-sizing: border-box;
    text-align: center;
    font-family: "Oswald", sans-serif;
    font-size: 29px;
    line-height: 40px;
    text-transform: uppercase;
    color: var(--ink);
    letter-spacing: 0.5px;
  }
  .contact-bar {
    position: absolute;
    left: 0;
    top: 1133px;
    width: 848px;
    height: 38px;
    display: flex;
    justify-content: space-between;
    align-items: center;
    padding: 0 14px;
    box-sizing: border-box;
    font-family: "Roboto Condensed", sans-serif;
    font-weight: 700;
    font-size: 20px;
    color: var(--white);
    text-transform: uppercase;
  }
  .contact-item {
    display: flex;
    align-items: center;
    gap: 8px;
  }
  .contact-dot {
    width: 16px;
    height: 16px;
    border-radius: 50%;
    background: var(--white);
  }
</style>
</head>
<body>
<main class="flyer">
  <svg class="flyer-shapes" width="848" height="1200" viewBox="0 0 848 1200">
    <defs>
      <linearGradient id="bamboo-tones" x1="0" y1="0" x2="1" y2="1">
        <stop offset="0" stop-color="#5d8a3a"/>
        <stop offset="0.45" stop-color="#a9c97a"/>
        <stop offset="1" stop-color="#3f6b2a"/>
      </linearGradient>
    </defs>
    <rect class="hero-photo" x="0" y="0" width="848" height="830" fill="url(#bamboo-tones)" role="img" aria-label="Photo: the retreat host in a lavender top with hands in prayer pose, standing in a green bamboo grove"/>
    <path class="top-sweep-blue" d="M0 0 H848 V40 Q 480 70 0 178 Z" fill="var(--sky)"/>
    <path class="top-sweep-white" d="M0 0 H848 V18 Q 460 40 0 140 Z" fill="var(--paper)"/>
    <path class="top-sweep-dark" d="M280 66 Q 600 28 848 8 V0 Q 560 20 280 66 Z" fill="var(--ink)"/>
    <path class="lower-sweep-blue" d="M0 770 Q 330 560 848 590 V660 Q 360 630 0 830 Z" fill="var(--sky)"/>
    <path class="lower-sweep-dark" d="M200 700 Q 520 590 848 612 V628 Q 520 600 200 700 Z" fill="var(--ink)"/>
    <path class="lower-panel" d="M0 830 Q 360 640 848 650 V1200 H0 Z" fill="var(--paper)"/>
    <polygon class="bonus-badge" transform="translate(730 440)" fill="var(--navy)" stroke="var(--white)" stroke-width="4"
      points="108,0 92.7,24.8 93.5,54 67.9,67.9 54,93.5 24.8,92.7 0,108 -24.8,92.7 -54,93.5 -67.9,67.9 -93.5,54 -92.7,24.8 -108,0 -92.7,-24.8 -93.5,-54 -67.9,-67.9 -54,-93.5 -24.8,-92.7 0,-108 24.8,-92.7 54,-93.5 67.9,-67.9 93.5,-54 92.7,-24.8"/>
    <path class="rule-top" d="M185 920 L460 918 L460 923 L185 924 Z" fill="var(--ink)"/>
    <path class="rule-bottom" d="M560 1003 L848 999 L848 1005 L560 1005 Z" fill="var(--ink)"/>
    <rect class="footer-accent" x="0" y="1124" width="848" height="5" fill="var(--sky)"/>
    <rect class="footer-bar" x="0" y="1133" width="848" height="38" fill="var(--ink)"/>
  </svg>

  <p class="host-signature">Marla Vosk</p>

  <p class="bonus-text">
    <span class="bonus-label">Bonus</span>
    <span class="bonus-detail">30 minute reiki<br>healing session</span>
  </p>

  <section class="event-details">
    <dl>
      <dt>Date</dt><dd>[Retreat dates]</dd>
      <dt>Time</dt><dd>[Start – finish]</dd>
      <dt>Place</dt><dd>[Venue, location]</dd>
      <dt>Price</dt><dd>[$000 per person]</dd>
    </dl>
    <p class="catering-note">Fully catered raw food &amp; juices. Price includes all accommodation, meals and workshops.</p>
  </section>

  <h1 class="retreat-title">
    <span class="title-out">Out</span>
    <span class="title-bloom">Bloom</span>
    <span class="title-the">the</span>
    <span class="title-spirit">Spirit</span>
  </h1>

  <p class="tagline">RETREAT INTO YOU</p>

  <p class="activities">Daily meditation, ecstatic dance,<br>spiritual development workshops on intuition</p>

  <footer class="contact-bar">
    <span class="contact-item"><span class="contact-dot"></span>www.marlavosk.com</span>
    <span class="contact-item"><span class="contact-dot"></span>www.pagenest.com/koruhaven</span>
  </footer>
</main>
</body>
</html>
```